Veluxa Bone & Motion Business Card

Need a business card using the logo provided. I want brand side of the card to be grey with the logo in the center of the card in white.

On the other side I leave to the designers

Target Market(s)

Personal Injury Attorneys

Industry/Entity Type

Medical

Contact Information for Business Card

Name, CEO. Cell Phone, (Brightwater, Address, Phone) (Cedar Glen, Address, Phone) (Northvale, Address, Phone)

Colors

Designer to choose only greyscale colors for use in the design.

Requirements
Must have
• Logo by itself on one side

```html
<!DOCTYPE html>
<html lang="en">
<head>
<meta charset="utf-8">
<title>Veluxa Bone &amp; Motion Business Card</title>
<link href="https://fonts.googleapis.com/css2?family=Lato:wght@400;700&family=Arimo:wght@400;700&display=swap" rel="stylesheet">
<style>
  :root{
    --page:#e4e4e2;
    --card-white:#ffffff;
    --brand-blue:#3a76b4;
    --slate:#95b1b9;
    --slate-deep:#6f8f98;
    --ink-grey:#6e6e6e;
    --rule-grey:#9a9a9a;
    --faint:#e9eef0;
  }
  *{box-sizing:border-box;margin:0;padding:0}
  html,body{width:1200px;height:802px;overflow:hidden;background:var(--page)}
  .stage{position:relative;width:1200px;height:802px}
  .card{position:absolute;width:540px;height:309px;overflow:hidden;box-shadow:0 6px 18px rgba(0,0,0,.12)}
  .card--front{left:40px;top:246px;background:var(--card-white);font-family:"Arimo",Arial,sans-serif}
  .card--back{left:620px;top:246px;background:var(--slate)}

  .front-decor{position:absolute;left:250px;top:0;width:290px;height:160px;
    background:linear-gradient(200deg,var(--faint) 0%,rgba(233,238,240,.6) 55%,rgba(255,255,255,0) 100%);
    border-bottom-left-radius:220px 120px}
  .brand-name{position:absolute;left:28px;top:46px;font-family:"Lato",sans-serif;font-weight:700;
    font-size:26px;line-height:1.15;letter-spacing:3px;color:var(--brand-blue);text-transform:uppercase}
  .brand-dot{position:absolute;left:28px;top:30px;width:9px;height:9px;border-radius:50%;background:var(--brand-blue)}

  .person{position:absolute;right:30px;top:92px;text-align:right}
  .person__name{font-weight:700;font-size:17px;color:var(--brand-blue);letter-spacing:.3px}
  .person__role{font-size:11px;color:var(--ink-grey);margin-top:2px}
  .person__rule{position:absolute;right:30px;top:138px;width:200px;height:1px;background:var(--rule-grey)}

  .cell{position:absolute;left:28px;top:150px;font-size:12px;color:var(--ink-grey);display:flex;align-items:center;gap:6px}
  .divider{position:absolute;left:20px;top:174px;width:500px;height:1px;background:var(--rule-grey)}

  .offices{position:absolute;left:28px;top:186px;width:490px;display:flex}
  .office{flex:1;padding-right:10px;font-size:11.5px;line-height:1.35;color:var(--ink-grey)}
  .office + .office{border-left:1px solid var(--rule-grey);padding-left:14px}
  .office__city{font-weight:700;color:var(--brand-blue);font-size:12.5px}
  .office__phone{display:flex;align-items:center;gap:5px;margin-top:1px}
  .front-band{position:absolute;left:0;bottom:0;width:100%;height:8px;background:var(--brand-blue)}

  .back-decor{position:absolute;left:0;top:0;width:540px;height:170px;
    background:linear-gradient(180deg,var(--slate-deep) 0%,#86a3ab 60%,rgba(149,177,185,0) 100%);
    border-bottom-left-radius:260px 90px}
  .back-brand{position:absolute;left:0;right:0;top:196px;text-align:center;font-family:"Lato",sans-serif;
    font-weight:700;font-size:30px;line-height:1.2;letter-spacing:6px;color:#ffffff;text-transform:uppercase}
</style>
</head>
<body>
<main class="stage">
  <section class="card card--front">
    <div class="front-decor" role="img" aria-label="Faint vertebrae illustration"></div>
    <div class="brand-dot"></div>
    <div class="brand-name">Veluxa<br>Bone &amp; Motion</div>

    <div class="person">
      <div class="person__name">MARCUS DELANE</div>
      <div class="person__role">CEO</div>
    </div>
    <div class="person__rule"></div>

    <div class="cell">
      <svg width="8" height="12" viewBox="0 0 8 12"><rect x="0.75" y="0.75" width="6.5" height="10.5" rx="1" fill="none" stroke="#3a76b4" stroke-width="1.5"/></svg>
      123-456-2100
    </div>
    <div class="divider"></div>

    <div class="offices">
      <div class="office">
        <div class="office__city">Brightwater</div>
        <div>Your Address, City</div>
        <div>State, Zip 0000</div>
        <div class="office__phone"><svg width="10" height="10" viewBox="0 0 10 10"><path d="M2 1 L4 3 L3 4.2 Q4.3 6 5.8 7 L7 6 L9 8 L7.6 9.4 Q3.5 8.6 0.6 2.4 Z" fill="#3a76b4"/></svg>123-456-2100</div>
      </div>
      <div class="office">
        <div class="office__city">Cedar Glen</div>
        <div>Your Address, City</div>
        <div>State, Zip 0000</div>
        <div class="office__phone"><svg width="10" height="10" viewBox="0 0 10 10"><path d="M2 1 L4 3 L3 4.2 Q4.3 6 5.8 7 L7 6 L9 8 L7.6 9.4 Q3.5 8.6 0.6 2.4 Z" fill="#3a76b4"/></svg>123-456-2100</div>
      </div>
      <div class="office">
        <div class="office__city">Northvale</div>
        <div>Your Address, City</div>
        <div>State, Zip 0000</div>
        <div class="office__phone"><svg width="10" height="10" viewBox="0 0 10 10"><path d="M2 1 L4 3 L3 4.2 Q4.3 6 5.8 7 L7 6 L9 8 L7.6 9.4 Q3.5 8.6 0.6 2.4 Z" fill="#3a76b4"/></svg>123-456-2100</div>
      </div>
    </div>
    <div class="front-band"></div>
  </section>

  <section class="card card--back">
    <div class="back-decor" role="img" aria-label="Row of embossed vertebrae illustration"></div>
    <div class="back-brand">Veluxa<br>Bone &amp; Motion</div>
  </section>
</main>
</body>
</html>
```